Need help in designing new business card utilizing our new logo.

BuildMark Solutions works with Construction Business Owners, Managers & IT Professionals to strengthen software usage and increase user productivity.

Our Construction Accounting and Mobile Field Management Software Clients engage with us in the following areas:

New Software Implementations
Software Re-Implementations
Redesigning Software Usage at the User Level
Project Coordination & Management
Continued Software Support

Old tag line:
Weighing Options - Implementing Solutions

www.buildmark-solutions.example

Ridge 4 is a product, but not needed for a new business card.

```html
<!DOCTYPE html>
<html lang="en">
<head>
<meta charset="utf-8">
<title>BuildMark Solutions – Business Card</title>
<link href="https://fonts.googleapis.com/css2?family=Montserrat:wght@400;500;600&display=swap" rel="stylesheet">
<style>
  :root {
    --stage: #2a2a2c;
    --brand-blue: #2c3492;
    --brand-blue-light: #3341a6;
    --paper: #ffffff;
    --paper-shade: #eeeef0;
    --ink-light: #ffffff;
  }
  * { box-sizing: border-box; margin: 0; padding: 0; }
  html, body {
    width: 1200px; height: 897px; overflow: hidden;
    background: var(--stage);
    font-family: "Montserrat", Arial, sans-serif;
  }
  .card {
    position: absolute; left: 304px; width: 594px; height: 338px;
    border-radius: 18px; overflow: hidden;
    background: linear-gradient(120deg, var(--brand-blue) 0%, var(--brand-blue-light) 100%);
    color: var(--ink-light);
  }
  .card--front { top: 92px; }
  .card--back { top: 470px; }

  .front-panel { position: absolute; inset: 0; }
  .identity { position: absolute; left: 30px; top: 30px; }
  .identity__name { font-size: 24px; font-weight: 600; letter-spacing: 0.2px; }
  .identity__role { font-size: 14px; font-weight: 400; margin-top: 2px; }

  .contact {
    position: absolute; left: 30px; top: 104px; width: 300px;
    list-style: none; font-size: 15px; line-height: 20px; white-space: nowrap;
  }
  .contact li { display: flex; align-items: center; gap: 8px; }
  .contact svg { width: 10px; height: 10px; flex: none; }

  .address { position: absolute; left: 30px; top: 195px; font-size: 15px; line-height: 21px; font-style: normal; }
  .specialty { position: absolute; left: 30px; top: 269px; font-size: 15px; line-height: 21px; }

  .brand {
    position: absolute; left: 365px; top: 145px;
    display: flex; align-items: center; gap: 10px;
  }
  .brand__mark { width: 14px; height: 14px; background: var(--brand-blue); flex: none; }
  .brand__name {
    font-size: 22px; font-weight: 600; line-height: 24px; color: var(--brand-blue);
  }

  .back-pattern { position: absolute; inset: 0; }
  .back-brand {
    position: absolute; left: 0; right: 0; top: 108px;
    display: flex; justify-content: center; align-items: center; gap: 12px;
  }
  .back-brand__mark { width: 18px; height: 18px; background: var(--ink-light); }
  .back-brand__name { font-size: 38px; font-weight: 600; color: var(--ink-light); }
  .services {
    position: absolute; left: 0; right: 0; top: 222px;
    list-style: none; text-align: center; font-size: 15.5px; line-height: 20px;
  }
</style>
</head>
<body>

<section class="card card--front">
  <svg class="front-panel" viewBox="0 0 594 338" width="594" height="338" aria-hidden="true">
    <defs>
      <linearGradient id="panelShade" x1="0" y1="0" x2="1" y2="1">
        <stop offset="0" stop-color="#ffffff"/>
        <stop offset="1" stop-color="#eeeef0"/>
      </linearGradient>
    </defs>
    <polygon points="484,0 338,84 338,256 484,338 594,338 594,0" fill="url(#panelShade)"/>
  </svg>

  <div class="identity">
    <h1 class="identity__name">Dana R. Whitfield</h1>
    <p class="identity__role">Owner</p>
  </div>

  <ul class="contact">
    <li>
      <svg viewBox="0 0 10 10"><path d="M2 0.5 L3.8 2.6 L2.8 3.6 Q4 6 6.4 7.2 L7.4 6.2 L9.5 8 L8.2 9.5 Q3 8.6 0.5 1.8 Z" fill="currentColor"/></svg>
      866-555-0142 ext.100
    </li>
    <li>
      <svg viewBox="0 0 10 10"><rect x="2.2" y="0.5" width="5.6" height="9" rx="1" fill="none" stroke="currentColor" stroke-width="1.2"/><rect x="4.2" y="7.2" width="1.6" height="1" fill="currentColor"/></svg>
      518-555-0193
    </li>
    <li>
      <svg viewBox="0 0 10 10"><rect x="0.6" y="2" width="8.8" height="6" fill="none" stroke="currentColor" stroke-width="1.1"/><path d="M0.6 2 L5 5.6 L9.4 2" fill="none" stroke="currentColor" stroke-width="1.1"/></svg>
      dana@buildmark-solutions.example
    </li>
    <li>
      <svg viewBox="0 0 10 10"><circle cx="5" cy="5" r="4.3" fill="none" stroke="currentColor" stroke-width="1"/><ellipse cx="5" cy="5" rx="1.8" ry="4.3" fill="none" stroke="currentColor" stroke-width="0.9"/><path d="M0.7 5 H9.3" stroke="currentColor" stroke-width="0.9"/></svg>
      www.buildmark-solutions.example
    </li>
  </ul>

  <address class="address">
    48 Juniper Avenue - PMB 117<br>
    Lakeview Falls NY 12000
  </address>

  <p class="specialty">Construction Accounting<br>Software Consultants</p>

  <div class="brand">
    <span class="brand__mark"></span>
    <span class="brand__name">BuildMark<br>Solutions</span>
  </div>
</section>

<section class="card card--back">
  <div class="back-pattern" role="img" aria-label="Faint repeating brand pattern across the blue background" style="background: linear-gradient(120deg, #2d3594 0%, #3a48ad 100%);"></div>

  <div class="back-brand">
    <span class="back-brand__mark"></span>
    <span class="back-brand__name">BuildMark Solutions</span>
  </div>

  <ul class="services">
    <li>New Software Implementations | Software Re-Implementations</li>
    <li>Redesigning Software Usage at the User Level</li>
    <li>Project Coordination &amp; Management</li>
    <li>Continued Software Support</li>
  </ul>
</section>

</body>
</html>
```